Graphic Design Project

Hi Designers
New Label for New Rum .
The label we would like is it to be modern and smart looking, simple and eye catching. Ingenuity is required and a great open mind to creating this label. Type of rum -Rich flavour with a smooth rounded character. It has robust fruity flavours of molasses, honey and chocolate and is not as sweet as other rums, giving it a strong dark rum taste for the "real rum drinker. If you google Crimson Reef Rum thats the type of bottle using .
Name is : Tarvey Amber
Size:1l
Alcohol :37.5% Imported Dark Rum
Final designer will be paid extra for posters and t shirt designs. email is dorin@velta-example.co.nz
Target Market(s)
Rum Drinkers .
Industry/Entity Type
Graphic Design
Look and feel
Each slider illustrates characteristics of the customer's brand and the style your logo design should communicate.

```html
<!DOCTYPE html>
<html lang="en">
<head>
<meta charset="utf-8">
<title>Tarvey Amber – Imported Dark Rum Label</title>
<link rel="stylesheet" href="https://fonts.googleapis.com/css2?family=Arimo:wght@400;700&family=Tinos:wght@700&family=Oswald:wght@600&display=swap">
<style>
  :root {
    --page: #ffffff;
    --label-black: #0b0705;
    --smoke-brown: #2a1a10;
    --smoke-deep: #160d08;
    --frame-gold: #e0b21c;
    --frame-glow: rgba(230, 180, 20, 0.55);
    --text-gold: #d9a51a;
    --pill-gold: #d6a21a;
    --ribbon-yellow: #f6b632;
    --ribbon-orange: #e8761c;
    --ribbon-red: #c3261d;
    --ship-light: #b86a1e;
    --ship-mid: #8c4a14;
    --ship-dark: #5a2c0c;
    --ink: #0a0a0a;
  }
  * { margin: 0; padding: 0; box-sizing: border-box; }
  html, body {
    width: 1200px;
    height: 999px;
    overflow: hidden;
    background: var(--page);
  }
  .label {
    position: absolute;
    left: 318px;
    top: 72px;
    width: 563px;
    height: 855px;
    border: 6px solid var(--frame-gold);
    box-shadow: 0 0 14px 4px var(--frame-glow);
    background:
      radial-gradient(ellipse 60% 35% at 25% 30%, var(--smoke-brown), transparent 70%),
      radial-gradient(ellipse 55% 30% at 80% 65%, var(--smoke-brown), transparent 70%),
      radial-gradient(ellipse 50% 25% at 40% 88%, var(--smoke-deep), transparent 70%),
      var(--label-black);
    overflow: hidden;
  }
  .ribbon-art {
    position: absolute;
    left: 50px;
    top: 86px;
    width: 463px;
    height: 112px;
    border-radius: 22px;
    background: linear-gradient(90deg, var(--ribbon-orange) 0%, var(--ribbon-yellow) 35%, var(--ribbon-orange) 70%, var(--ribbon-red) 100%);
  }
  .brand-name {
    position: absolute;
    left: 0;
    right: 0;
    top: 118px;
    text-align: center;
    font-family: "Oswald", sans-serif;
    font-weight: 600;
    font-size: 46px;
    line-height: 1;
    color: var(--ink);
  }
  .ship-art {
    position: absolute;
    left: 112px;
    top: 214px;
    width: 318px;
    height: 340px;
    border-radius: 42% 48% 40% 46%;
    background: radial-gradient(ellipse at 50% 45%, var(--ship-light) 0%, var(--ship-mid) 55%, var(--ship-dark) 100%);
  }
  .rum-type {
    position: absolute;
    left: 0;
    right: 0;
    top: 580px;
    text-align: center;
    font-family: "Arimo", sans-serif;
    font-weight: 700;
    font-size: 30px;
    line-height: 36px;
    color: var(--text-gold);
  }
  .producer {
    position: absolute;
    left: 84px;
    top: 716px;
    width: 392px;
    height: 38px;
    border-radius: 19px;
    background: var(--pill-gold);
    text-align: center;
    font-family: "Tinos", serif;
    font-weight: 700;
    font-size: 24px;
    line-height: 38px;
    color: var(--ink);
  }
  .volume {
    position: absolute;
    left: 18px;
    top: 776px;
    font-family: "Arimo", sans-serif;
    font-weight: 400;
    font-size: 42px;
    line-height: 48px;
    color: var(--text-gold);
  }
  .strength {
    position: absolute;
    right: 28px;
    top: 792px;
    font-family: "Arimo", sans-serif;
    font-size: 21px;
    line-height: 26px;
    color: var(--text-gold);
  }
</style>
</head>
<body>
  <main class="label">
    <div class="ribbon-art" role="img" aria-label="Curled banner ribbon in amber, orange and red behind the brand name"></div>
    <p class="brand-name">Tarvey Amber</p>
    <div class="ship-art" role="img" aria-label="Illustration of a tall sailing galleon in amber and brown tones"></div>
    <p class="rum-type">Imported Dark Rum</p>
    <p class="producer">Produced by Norvane Ltd.</p>
    <p class="volume">1l</p>
    <p class="strength">37.5%vol.</p>
  </main>
</body>
</html>
```